Trade Show Booth Wall Graphics Design (Beauty Industry)

We are a beauty/nail supply distributor that supplies products used in professional nail salons. Our target customers are Nail Salons. We are looking for a wall panel graphic design that will be placed on the walls of our trade show booth (see attached image for reference).
These wall panels will act as an aesthetic background and highlight the key product offerings to customers as they view our booth. The primary goal of each wall panel design should focus on the product name and image. Backgrounds for each wall panel may include professional/stock photography to give context or visualization, color pattern or wave design to create a sense of “flow” between products, and/or any general use of colors to provide a professional, simple, and clear product message to viewers.
Each wall panel, and designated products, is based on product category and similarity of function/use.
Nail Salons
Beauty

```html
<!DOCTYPE html>
<html lang="en">
<head>
<meta charset="utf-8">
<title>Booth Wall Panels</title>
<link href="https://fonts.googleapis.com/css2?family=Yeseva+One&display=swap" rel="stylesheet">
<style>
  :root {
    --stage: #4a4a4a;
    --orange: #ec680c;
    --red: #dc3d4a;
    --magenta: #c01ba6;
    --purple: #9b2cc8;
    --sky: #d9f1fb;
    --sky-deep: #4fb3ea;
    --white: #ffffff;
    --divider: #2a2a2a;
  }
  * { margin: 0; padding: 0; box-sizing: border-box; }
  html, body { width: 1200px; height: 900px; overflow: hidden; }
  body { background: var(--stage); position: relative; font-family: "Yeseva One", serif; }
  .booth-wall { position: absolute; left: 0; top: 97px; width: 1200px; height: 705px; overflow: hidden; }
  .wall-art { position: absolute; inset: 0; width: 100%; height: 100%; }
  .panel { position: absolute; top: 0; width: 300px; height: 705px; }
  .panel--waxing { left: 0; }
  .panel--color { left: 300px; }
  .panel--kits { left: 600px; }
  .panel--files { left: 900px; }
  .headline { position: absolute; color: var(--white); line-height: 1; white-space: nowrap; }
  .product { position: absolute; border-radius: 8px; box-shadow: 0 4px 10px rgba(0,0,0,.15); }
  .product--wax-bags { background: linear-gradient(90deg, #3a35a8 0 50%, #f07b2e 50% 100%); }
  .product--tape { background: linear-gradient(135deg, #ffffff, #e6e9ee); border-radius: 40px 8px 8px 40px; }
  .product--tins { background: linear-gradient(90deg, #f7d6e2, #e0f1f7 50%, #fbe9a6); border-radius: 14px; }
  .product--film { background: linear-gradient(90deg, #e8eef1, #f6e7d8); }
  .product--gel-small { background: linear-gradient(180deg, #b9bcc2 0 30%, #ffffff 30% 100%); }
  .product--gel-large { background: linear-gradient(180deg, #2c1e14 0 20%, #6b3a1a 20% 100%); }
  .product--pedi-kit { background: linear-gradient(135deg, #ffffff, #b48be0); }
  .product--mani-kit { background: linear-gradient(135deg, #ffffff, #dcd6ee); }
  .product--caps { background: linear-gradient(90deg, #4a9ee6, #eef2f6); border-radius: 30px; }
  .product--pouch { background: linear-gradient(180deg, #9ccbe0, #ffffff); }
  .product--file-pack { background: linear-gradient(135deg, #9aa6b4, #d5dbe2); }
  .product--buffers { background: linear-gradient(135deg, #2b2b2b, #f47a3c 55%, #8a4fd8); }
  .product--file-pack-light { background: linear-gradient(135deg, #f1f1f1, #c9d1d8); }
</style>
</head>
<body>
<section class="booth-wall">
  <svg class="wall-art" viewBox="0 0 1592 935" preserveAspectRatio="none" aria-hidden="true">
    <defs>
      <linearGradient id="head-grad" x1="0" x2="1" y1="0" y2="0">
        <stop offset="0" stop-color="var(--orange)"/>
        <stop offset="0.45" stop-color="var(--red)"/>
        <stop offset="1" stop-color="var(--magenta)"/>
      </linearGradient>
      <linearGradient id="foot-grad" x1="0" x2="1" y1="0" y2="0">
        <stop offset="0" stop-color="var(--magenta)"/>
        <stop offset="0.55" stop-color="var(--red)"/>
        <stop offset="1" stop-color="var(--orange)"/>
      </linearGradient>
      <linearGradient id="sky-grad" x1="0" x2="0" y1="0" y2="1">
        <stop offset="0" stop-color="var(--sky)"/>
        <stop offset="1" stop-color="#bfe6f8"/>
      </linearGradient>
    </defs>
    <rect width="1592" height="935" fill="url(#sky-grad)"/>
    <path d="M0,620 C300,560 600,720 900,640 C1200,560 1400,700 1592,620 V700 C1400,780 1200,640 900,720 C600,800 300,650 0,700 Z" fill="var(--sky-deep)" opacity=".35"/>
    <path d="M0,760 C350,690 650,850 1000,760 C1250,700 1450,790 1592,740 V790 C1450,840 1250,760 1000,820 C650,900 350,750 0,820 Z" fill="#2f8fd8" opacity=".3"/>
    <path d="M0,270 C120,320 300,305 400,302 C500,300 580,340 700,350 C820,360 880,270 990,245 C1050,230 1130,255 1250,280 C1350,300 1450,300 1592,235 V0 H0 Z" fill="var(--purple)"/>
    <path d="M0,230 C120,280 300,265 400,262 C500,260 580,300 700,310 C820,320 880,230 990,205 C1050,190 1130,215 1250,240 C1350,260 1450,260 1592,195" fill="none" stroke="var(--white)" stroke-width="8"/>
    <path d="M0,0 H1592 V195 C1450,260 1350,260 1250,240 C1130,215 1050,190 990,205 C880,230 820,320 700,310 C580,300 500,260 400,262 C300,265 120,280 0,230 Z" fill="url(#head-grad)"/>
    <path d="M0,935 V880 C150,820 300,830 400,870 C550,910 650,870 800,850 C950,830 1100,800 1250,830 C1400,860 1500,800 1592,790 V935 Z" fill="url(#foot-grad)"/>
    <g stroke="var(--divider)" stroke-width="2">
      <line x1="398" y1="0" x2="398" y2="935"/>
      <line x1="796" y1="0" x2="796" y2="935"/>
      <line x1="1194" y1="0" x2="1194" y2="935"/>
    </g>
  </svg>

  <div class="panel panel--waxing">
    <h2 class="headline" style="left:38px;top:52px;font-size:54px">Calm &amp;</h2>
    <p class="headline" style="left:107px;top:102px;font-size:32px">Gentle</p>
    <p class="headline" style="left:42px;top:124px;font-size:60px">Waxing</p>
    <div class="product product--wax-bags" style="left:35px;top:219px;width:115px;height:162px" role="img" aria-label="Paraffin wax bags"></div>
    <div class="product product--tape" style="left:140px;top:300px;width:135px;height:85px" role="img" aria-label="Waxing strip roll"></div>
    <div class="product product--tins" style="left:22px;top:400px;width:258px;height:95px" role="img" aria-label="Three wax tins"></div>
    <div class="product product--film" style="left:20px;top:505px;width:260px;height:100px" role="img" aria-label="Roll of waxing film"></div>
  </div>

  <div class="panel panel--color">
    <h2 class="headline" style="left:68px;top:47px;font-size:35px">Brilliant</h2>
    <p class="headline" style="left:32px;top:78px;font-size:58px">Shine &amp;</p>
    <p class="headline" style="left:70px;top:128px;font-size:35px">Rich</p>
    <p class="headline" style="left:32px;top:155px;font-size:60px">Colors</p>
    <div class="product product--gel-small" style="left:30px;top:247px;width:240px;height:177px" role="img" aria-label="Four small gel polish bottles"></div>
    <div class="product product--gel-large" style="left:24px;top:442px;width:252px;height:177px" role="img" aria-label="Four large gel refill bottles"></div>
  </div>

  <div class="panel panel--kits">
    <h2 class="headline" style="left:33px;top:47px;font-size:26px">Individual</h2>
    <p class="headline" style="left:33px;top:73px;font-size:46px">Perfection</p>
    <div class="product product--pedi-kit" style="left:45px;top:175px;width:205px;height:113px" role="img" aria-label="Disposable pedicure kit"></div>
    <div class="product product--mani-kit" style="left:48px;top:299px;width:213px;height:117px" role="img" aria-label="Disposable manicure kit"></div>
    <div class="product product--caps" style="left:35px;top:424px;width:230px;height:64px" role="img" aria-label="Disposable tub liners"></div>
    <div class="product product--pouch" style="left:55px;top:495px;width:192px;height:140px" role="img" aria-label="Sterilization pouches"></div>
  </div>

  <div class="panel panel--files">
    <p class="headline" style="left:65px;top:48px;font-size:24px">The</p>
    <h2 class="headline" style="left:20px;top:64px;font-size:46px">Foundation</h2>
    <p class="headline" style="left:65px;top:105px;font-size:24px">of Every</p>
    <p class="headline" style="left:20px;top:120px;font-size:46px">Manicure</p>
    <div class="product product--file-pack" style="left:56px;top:186px;width:215px;height:151px" role="img" aria-label="Pack of zebra nail files"></div>
    <div class="product product--buffers" style="left:33px;top:345px;width:230px;height:136px" role="img" aria-label="Sanding buffer blocks"></div>
    <div class="product product--file-pack-light" style="left:63px;top:491px;width:207px;height:158px" role="img" aria-label="Pack of medium nail files"></div>
  </div>
</section>
</body>
</html>
```